New Business Card Design Project LORVANTI-Italy

we are LORVANTI-Italy
our company in the market for 3 years we are luxury cosmetic company and its about time for a facelift :)
i will like to have elegant luxurious and unique business card
that will give the person that get it a unique, luxurious and elegant impression
I'm VERY OPEN FOR NEW IDEAS , even duo i add a few files of things that i see on line and i like them

i add my logo as well
my website is LORVANTI.COM
(if you would like to see the main style that we have)

Target Market(s)

adult that have money :)

Industry/Entity Type

Business

Contact Information for Business Card

Name - Dario Lorvanti
Position - CEO and CO Founder
address - 4817 E Halvern
telephone - 555-384-1926
email - dario@lorvanti.com
fax - 555-384-1926
website - LORVANTI.COM

Colors
000000
959595
fbee3e
ffffff

Requirements
Must have
• big logo in GOLD color
• elegant look
• impressive
Nice to have
• not must but maybe classy pattern background
• not must but maybe emblem
• maybe clear plastic business card
Should not have
• colors
• images

```html
<!DOCTYPE html>
<html lang="en">
<head>
<meta charset="utf-8">
<title>LORVANTI Italy – Business Card</title>
<link href="https://fonts.googleapis.com/css2?family=Cinzel:wght@400;500&family=Roboto:wght@400&display=swap" rel="stylesheet">
<style>
  :root {
    --page-bg: #e6e3df;
    --card-black: #151515;
    --card-black-light: #2a2a2a;
    --card-white: #ffffff;
    --gold: #c59d3f;
    --gold-band: #d9b44a;
    --ink: #2b2b2b;
  }
  * { margin: 0; padding: 0; box-sizing: border-box; }
  html, body {
    width: 1200px; height: 1200px; overflow: hidden;
    background: var(--page-bg);
  }
  .canvas { position: relative; width: 1200px; height: 1200px; }

  .card {
    position: absolute; left: 214px; width: 773px; height: 442px;
    box-shadow: 0 6px 16px rgba(0,0,0,0.25);
    overflow: hidden;
  }
  .card--back { top: 149px; display: flex; background: var(--card-white); }
  .card--front { top: 633px; }

  .pattern-field {
    background: radial-gradient(ellipse at 50% 45%, var(--card-black-light) 0%, var(--card-black) 75%);
  }

  .brand-panel { position: relative; width: 382px; height: 100%; }
  .gold-band { width: 7px; height: 100%; background: var(--gold-band); }

  .brand-mark { position: absolute; left: 0; right: 0; text-align: center; }
  .brand-mark__circle {
    display: block; margin: 0 auto;
    border: 3px solid var(--gold); border-radius: 50%;
  }
  .brand-mark__name {
    display: block;
    font-family: 'Cinzel', serif; font-weight: 500;
    color: var(--gold); letter-spacing: 1px; line-height: 1;
  }

  .brand-panel .brand-mark { top: 96px; }
  .brand-panel .brand-mark__circle { width: 126px; height: 126px; }
  .brand-panel .brand-mark__name { font-size: 46px; margin-top: 30px; }

  .card--front .brand-mark { top: 78px; }
  .card--front .brand-mark__circle { width: 146px; height: 146px; }
  .card--front .brand-mark__name { font-size: 60px; margin-top: 36px; }

  .contact-panel { position: relative; flex: 1; padding: 88px 0 0 41px; }
  .person__name {
    font-family: 'Cinzel', serif; font-weight: 500; font-size: 33px;
    color: var(--gold); letter-spacing: 1.5px; line-height: 1;
  }
  .person__role {
    font-family: 'Roboto', sans-serif; font-size: 19px;
    color: var(--ink); margin-top: 8px;
  }
  .contact-list { list-style: none; margin-top: 50px; }
  .contact-list li {
    display: flex; align-items: center; height: 31px;
    font-family: 'Roboto', sans-serif; font-size: 18.5px; color: var(--ink);
  }
  .contact-list svg {
    width: 17px; height: 17px; margin-right: 14px; flex: none;
    fill: none; stroke: var(--gold); stroke-width: 1.6;
    stroke-linecap: round; stroke-linejoin: round;
  }
</style>
</head>
<body>
<main class="canvas">

  <section class="card card--back">
    <div class="brand-panel pattern-field" role="img" aria-label="Black card face with a fine diamond lattice pattern">
      <div class="brand-mark">
        <span class="brand-mark__circle"></span>
        <span class="brand-mark__name">LORVANTI</span>
      </div>
    </div>
    <div class="gold-band"></div>
    <div class="contact-panel">
      <h1 class="person__name">DARIO LORVANTI</h1>
      <p class="person__role">CEO and CO Founder</p>
      <ul class="contact-list">
        <li>
          <svg viewBox="0 0 24 24"><path d="M5 3h4l2 5-2.5 1.5a11 11 0 0 0 6 6L16 13l5 2v4a2 2 0 0 1-2 2A17 17 0 0 1 3 5a2 2 0 0 1 2-2z"/></svg>
          555-384-1926
        </li>
        <li>
          <svg viewBox="0 0 24 24"><rect x="6" y="3" width="12" height="6"/><rect x="3" y="9" width="18" height="8" rx="1"/><rect x="7" y="14" width="10" height="7"/></svg>
          555-384-1926
        </li>
        <li>
          <svg viewBox="0 0 24 24"><rect x="3" y="5" width="18" height="14"/><path d="M3 5l9 8 9-8"/></svg>
          dario@lorvanti.com
        </li>
        <li>
          <svg viewBox="0 0 24 24"><circle cx="12" cy="12" r="9"/><path d="M3 12h18M12 3c3 3 3 15 0 18M12 3c-3 3-3 15 0 18"/></svg>
          www.lorvanti.com
        </li>
        <li>
          <svg viewBox="0 0 24 24"><path d="M12 22s-7-7-7-12a7 7 0 0 1 14 0c0 5-7 12-7 12z"/><circle cx="12" cy="10" r="2.5"/></svg>
          4817 E Halvern
        </li>
      </ul>
    </div>
  </section>

  <section class="card card--front pattern-field" role="img" aria-label="Black card face with a fine diamond lattice pattern">
    <div class="brand-mark">
      <span class="brand-mark__circle"></span>
      <span class="brand-mark__name">LORVANTI</span>
    </div>
  </section>

</main>
</body>
</html>
```